Business Card, A4 Letter Head and DL Envelope for Brandvelle

We are looking for a design for our Business Card, A4 Letter Head and DL Envelope.

Brandvelle is a distributor of promotional products. We specialize in a range of branded promotional products, these include pens, polo shirts, key rings, drink bottles, uniforms and bags to name a few. We are experts in marketing and assist companies in choosing the right promotional product for their needs. We will predominately be an online business where customers visit our website and browse our range of promotional products and branding options.

Our colours are black, red, white and grey.

Files must be supplied in eps, pdf and ai format.

Please display the following information:
Derek Halloway
Account Manager
Suite xxx, 212 Ferrow Lane Melbourne, Victoria 3000
Phone +61 3 5550 1827
Mobile +61 455 016 342
sales@brandvelle-example.com.au
www.brandvelle-example.com.au

```html
<!DOCTYPE html>
<html lang="en">
<head>
<meta charset="utf-8">
<title>Brandvelle Stationery</title>
<link href="https://fonts.googleapis.com/css2?family=Questrial&display=swap" rel="stylesheet">
<style>
  :root {
    --backdrop: #737373;
    --paper: #ffffff;
    --brand-red: #d61f26;
    --brand-red-dark: #c01c22;
    --brand-red-light: #ed1c24;
    --ink: #1a1a1a;
    --grey: #4a4a4a;
    --faint: #ededed;
  }
  * { margin: 0; padding: 0; box-sizing: border-box; }
  html, body { width: 1200px; height: 785px; overflow: hidden; }
  body {
    background: var(--backdrop);
    font-family: "Questrial", sans-serif;
    position: relative;
  }
  .sheet {
    position: absolute;
    top: 48px;
    width: 530px;
    height: 680px;
    background: var(--paper);
    box-shadow: 3px 4px 6px rgba(0,0,0,0.35);
    overflow: hidden;
  }
  .letterhead { left: 49px; }
  .cover { left: 627px; }

  .letterhead-swoosh { position: absolute; left: 0; top: 0; }
  .letterhead-brand {
    position: absolute;
    left: 318px;
    top: 16px;
    display: flex;
    align-items: center;
    gap: 8px;
  }
  .brand-dot {
    width: 30px; height: 30px;
    border-radius: 50%;
    background: var(--brand-red);
  }
  .brand-name {
    color: var(--grey);
    letter-spacing: 0.5px;
    text-transform: uppercase;
  }
  .letterhead-brand .brand-name { font-size: 17px; }
  .watermark-circle {
    position: absolute;
    left: 350px;
    top: 455px;
    width: 150px; height: 150px;
    border-radius: 50%;
    background: var(--faint);
    opacity: 0.7;
  }
  .contact {
    position: absolute;
    left: 0; right: 0;
    text-align: center;
    font-size: 7px;
    line-height: 11px;
    color: var(--ink);
  }
  .contact .sep { color: var(--brand-red); margin: 0 3px; }
  .letterhead .contact { top: 645px; }
  .letterhead-base {
    position: absolute;
    left: 0; bottom: 0;
    width: 100%; height: 9px;
    background: var(--brand-red);
  }

  .cover-panel { position: absolute; left: 0; top: 0; }
  .cover-brand {
    position: absolute;
    left: 0; right: 0;
    top: 392px;
    display: flex;
    flex-direction: column;
    align-items: center;
    gap: 24px;
  }
  .cover-brand .brand-dot { width: 140px; height: 140px; }
  .cover-brand .brand-name { font-size: 42px; letter-spacing: 1px; }
  .cover .contact { top: 643px; }
</style>
</head>
<body>
  <section class="sheet letterhead">
    <svg class="letterhead-swoosh" width="530" height="110" viewBox="0 0 530 110">
      <path d="M0 0 H296 V52 C190 50 70 66 0 100 Z" fill="var(--brand-red-light)"/>
      <path d="M0 0 H296 V40 C190 36 70 48 0 62 Z" fill="var(--brand-red)"/>
    </svg>
    <div class="letterhead-brand">
      <span class="brand-dot"></span>
      <span class="brand-name">Brandvelle</span>
    </div>
    <div class="watermark-circle"></div>
    <div class="contact">
      <p>www.brandvelle-example.com.au<span class="sep">|</span>Suite xxx, 212 Ferrow Lane, Melbourne, Victoria 3000</p>
      <p>Tel: +61 3 5550 1827<span class="sep">|</span>Mob: +61 455 016 342<span class="sep">|</span>e-mail : sales@brandvelle-example.com.au</p>
    </div>
    <div class="letterhead-base"></div>
  </section>

  <section class="sheet cover">
    <svg class="cover-panel" width="530" height="340" viewBox="0 0 530 340">
      <rect width="530" height="340" fill="var(--brand-red-dark)"/>
      <path d="M0 340 C90 200 290 90 530 70 V340 Z" fill="var(--brand-red)"/>
      <path d="M120 340 C220 230 370 170 530 150 V340 Z" fill="var(--brand-red)" opacity="0.6"/>
    </svg>
    <div class="cover-brand">
      <span class="brand-dot"></span>
      <span class="brand-name">Brandvelle</span>
    </div>
    <div class="contact">
      <p>www.brandvelle-example.com.au<span class="sep">|</span>Suite xxx, 212 Ferrow Lane, Melbourne, Victoria 3000</p>
      <p>Tel: +61 3 5550 1827<span class="sep">|</span>Mob: +61 455 016 342<span class="sep">|</span>e-mail : sales@brandvelle-example.com.au</p>
    </div>
  </section>
</body>
</html>
```